Bridgeway Health of Nations

Please design a business card that is colorful but at the same time easy to read. We are based out on Miami Florida. We are a small start up healthcare company that has been in operation for 1 year. Our clients are Hospitals, Insurance companies, and Manage Care health companies. We are growing quickly and lead the niche we are in. Please make the card 2 sided on the front will be the typical info. Logo, Company Name, Persons Name, Title, Cell #, Office #, Fax#, email, website. No address. On the back we will list 5 services that we do. For example Care Transitions, Case management, Risk assessment, Utilization Review.
Target Market(s)
CEO's and COO's of hospitals and healthcare companies.
Industry/Entity Type
Healthcare

```html
<!DOCTYPE html>
<html lang="en">
<head>
<meta charset="utf-8">
<title>Bridgeway Health of Nations – Business Card</title>
<link href="https://fonts.googleapis.com/css2?family=Open+Sans:wght@400;600;700&display=swap" rel="stylesheet">
<style>
  :root {
    --page: #e9e7e3;
    --card: #f1f1f1;
    --navy: #252f8a;
    --blue-deep: #1f3fa6;
    --blue-light: #1f8fd6;
    --green: #1aa33c;
    --yellow: #e6d21a;
    --red: #d9242b;
    --ink: #4a4a4a;
    --ink-soft: #5d5d5d;
  }
  * { box-sizing: border-box; margin: 0; padding: 0; }
  html, body { width: 1200px; height: 900px; overflow: hidden; }
  body {
    background: var(--page);
    font-family: "Open Sans", Arial, sans-serif;
    position: relative;
  }
  .card {
    position: absolute;
    left: 280px;
    width: 640px;
    height: 366px;
    background: var(--card);
    overflow: hidden;
    box-shadow: 0 2px 10px rgba(0,0,0,0.12);
  }
  .card--back { top: 60px; }
  .card--front { top: 474px; }

  /* colour stripe */
  .stripe { position: absolute; left: 0; right: 0; height: 6px; display: flex; }
  .stripe span { flex: 1; }
  .stripe .s-green { background: var(--green); }
  .stripe .s-yellow { background: var(--yellow); }
  .stripe .s-red { background: var(--red); }

  /* back side */
  .back-brand {
    position: absolute; left: 60px; top: 70px;
    display: flex; align-items: center; gap: 22px;
  }
  .brand-dot { width: 70px; height: 70px; border-radius: 50%; background: var(--blue-deep); }
  .brand-name {
    color: var(--navy); font-weight: 700; font-size: 32px; line-height: 1.05;
  }
  .card--back .stripe { top: 196px; }
  .services {
    position: absolute; left: 0; right: 0; top: 202px; bottom: 0;
    background: linear-gradient(100deg, var(--blue-deep) 0%, var(--blue-light) 100%);
    color: #fff; font-size: 21px;
    padding: 42px 0 0 120px; line-height: 1.7;
  }
  .services li { display: inline; list-style: none; margin-right: 16px; }
  .services li::before { content: "• "; }

  /* front side */
  .front-brand {
    position: absolute; left: 56px; top: 110px; width: 230px;
    display: flex; flex-direction: column; align-items: center; gap: 16px;
  }
  .front-brand .brand-dot { width: 90px; height: 90px; }
  .front-brand .brand-name { font-size: 22px; text-align: center; }
  .person { position: absolute; left: 330px; top: 46px; color: var(--ink); }
  .person-name { font-size: 26px; font-weight: 400; letter-spacing: 0.5px; text-transform: uppercase; }
  .person-title { font-size: 14px; color: var(--ink-soft); margin-top: 2px; }
  .contacts { list-style: none; margin-top: 22px; font-size: 14.5px; line-height: 1.45; color: var(--ink); }
  .contacts b { display: inline-block; width: 18px; font-weight: 700; }
  .c-t b { color: var(--navy); }
  .c-m b { color: var(--green); }
  .c-f b { color: var(--yellow); }
  .c-e b { color: var(--red); }
  .website { margin-top: 24px; font-weight: 700; font-size: 15px; color: var(--ink); }
  .card--front .stripe { bottom: 0; height: 7px; }
</style>
</head>
<body>

  <section class="card card--back" aria-label="Business card, back">
    <div class="back-brand">
      <span class="brand-dot"></span>
      <div class="brand-name">Bridgeway Health<br>of Nations</div>
    </div>
    <div class="stripe"><span class="s-green"></span><span class="s-yellow"></span><span class="s-red"></span></div>
    <ul class="services">
      <li>Care Transitions</li><li>Case management</li><br>
      <li>Risk assessment</li><li>Utilization Review</li>
    </ul>
  </section>

  <section class="card card--front" aria-label="Business card, front">
    <div class="front-brand">
      <span class="brand-dot"></span>
      <div class="brand-name">Bridgeway Health of Nations</div>
    </div>
    <div class="person">
      <h1 class="person-name">Marcus Delaney</h1>
      <p class="person-title">Operation Manager</p>
      <ul class="contacts">
        <li class="c-t"><b>T</b>(305) 41 620 77 14</li>
        <li class="c-m"><b>M</b>(305) 88 214 39 06</li>
        <li class="c-f"><b>F</b>(305) 41 620 77 52</li>
        <li class="c-e"><b>E</b>marcus@bridgewayhealth.com</li>
      </ul>
      <p class="website">www.bridgewayhealth.com</p>
    </div>
    <div class="stripe"><span class="s-green"></span><span class="s-yellow"></span><span class="s-red"></span></div>
  </section>

</body>
</html>
```